Brellwick Partners, LLC Stationary

Brellwick Partners, LLC is a new financial planning and consulting company. We are looking for designs on business cards, letterhead, envelopes, and anything else that would be useful. Our preference for business card design is two sided. We are looking for a professional and clean look with incorporating the logo and patriotic feel. Thank you to all who participate and good luck!

```html
<!DOCTYPE html>
<html lang="en">
<head>
<meta charset="utf-8">
<title>Brellwick Partners, LLC — Business Card</title>
<link rel="stylesheet" href="https://fonts.googleapis.com/css2?family=Arimo:wght@400;700&family=Michroma&display=swap">
<style>
  :root {
    --navy: #1c3f6e;
    --red: #c8202b;
    --ink: #4a4d52;
    --paper: #ffffff;
    --backdrop: #e9e7e3;
    --rule: #d9d9d9;
  }
  * { box-sizing: border-box; margin: 0; padding: 0; }
  html, body { width: 1200px; height: 950px; overflow: hidden; }
  body {
    background: var(--backdrop);
    font-family: "Arimo", Arial, sans-serif;
    display: flex;
    flex-direction: column;
    align-items: center;
    justify-content: center;
    gap: 60px;
  }
  .card {
    width: 600px;
    height: 343px;
    background: var(--paper);
    border: 1px solid var(--rule);
    position: relative;
  }
  /* back side */
  .card--back { display: flex; flex-direction: column; align-items: center; justify-content: center; }
  .brand { display: flex; align-items: center; gap: 16px; }
  .brand__dot { width: 34px; height: 34px; border-radius: 50%; background: var(--navy); flex: none; }
  .brand__name {
    font-family: "Michroma", sans-serif;
    color: var(--navy);
    font-size: 22px;
    letter-spacing: 1px;
    line-height: 1.2;
  }
  .tagline {
    font-family: "Arimo", sans-serif;
    color: var(--red);
    font-size: 10px;
    letter-spacing: 2px;
    text-transform: uppercase;
    margin-top: 8px;
    padding-top: 6px;
    border-top: 1px solid var(--red);
  }
  .card--back .tagline { margin-left: 50px; }
  .card--back .web {
    position: absolute;
    bottom: 34px;
    left: 0; right: 0;
    text-align: center;
    font-size: 14px;
    letter-spacing: 4px;
    color: var(--ink);
  }
  /* front side */
  .contact {
    position: absolute;
    top: 34px;
    right: 36px;
    text-align: right;
    color: var(--ink);
    font-size: 14px;
    line-height: 1.45;
  }
  .contact__name { font-family: "Michroma", sans-serif; color: var(--navy); font-size: 16px; letter-spacing: 1px; }
  .contact__role { color: var(--red); font-size: 13px; letter-spacing: 1px; margin-bottom: 4px; }
  .contact__line { display: flex; justify-content: flex-end; align-items: center; gap: 7px; }
  .icon { width: 13px; height: 13px; fill: var(--navy); flex: none; }
  .card--front .brand-block {
    position: absolute;
    right: 36px;
    bottom: 30px;
    text-align: right;
  }
  .card--front .brand__name { font-size: 24px; }
</style>
</head>
<body>
  <section class="card card--back" aria-label="Business card, back">
    <div class="brand">
      <span class="brand__dot"></span>
      <span class="brand__name">Brellwick Partners, LLC</span>
    </div>
    <p class="tagline">Financial planning and consulting</p>
    <p class="web">www.brellwick.com</p>
  </section>

  <section class="card card--front" aria-label="Business card, front">
    <div class="contact">
      <p class="contact__name">MARCUS HALE</p>
      <p class="contact__role">PRESIDENT</p>
      <p class="contact__line">2417 Ashbury Lane</p>
      <p class="contact__line">Glen Cove, NY 11542</p>
      <p class="contact__line">555 0142 7780
        <svg class="icon" viewBox="0 0 16 16" aria-hidden="true"><path d="M3 1l3 3-2 2c1 2 3 4 5 5l2-2 3 3-2 3C7 15 1 9 1 3z"/></svg></p>
      <p class="contact__line">555 0193 4461
        <svg class="icon" viewBox="0 0 16 16" aria-hidden="true"><rect x="4" y="1" width="8" height="4"/><rect x="1" y="6" width="14" height="6" rx="1"/><rect x="4" y="10" width="8" height="5" fill="#fff" stroke="#1c3f6e" stroke-width="1.5"/></svg></p>
      <p class="contact__line">marcus@brellwick.com
        <svg class="icon" viewBox="0 0 16 16" aria-hidden="true"><rect x="1" y="3" width="14" height="10" rx="1"/><path d="M1.5 4l6.5 5 6.5-5" fill="none" stroke="#fff" stroke-width="1.4"/></svg></p>
      <p class="contact__line">www.brellwick.com
        <svg class="icon" viewBox="0 0 16 16" aria-hidden="true"><circle cx="8" cy="8" r="7"/><path d="M1 8h14M8 1c-3 4-3 10 0 14M8 1c3 4 3 10 0 14" fill="none" stroke="#fff" stroke-width="1.1"/></svg></p>
    </div>
    <div class="brand-block">
      <p class="brand__name">Brellwick Partners, LLC</p>
      <p class="tagline">Financial planning and consulting</p>
    </div>
  </section>
</body>
</html>
```